Website Design - TallyPorchHelpers.net

PLEASE CHECK WORD DOCUMENT ATTACHED FOR WEBSITE FLOW.

Target Market(s)

REAL ESTATE AGENTS ARE THE TARGET MARKET

Industry/Entity Type

Real Estate

Coding

Coded - Design and coding required

Number of Pages Required

4 page

Colors

Designer to choose colors to be used in the design.

Requirements
Must have
• WE LIKE RED LOGO ATTACHED
Nice to have
• PLEASE CHECK WORD DOCUMENT ATTACHED FOR WEBSITE FLOW.
Should not have

```html
<!DOCTYPE html>
<html lang="en">
<head>
<meta charset="utf-8">
<title>TallyPorchHelpers.net</title>
<link rel="stylesheet" href="https://fonts.googleapis.com/css2?family=Lato:wght@400;700;900&family=Poppins:wght@400;500;600&display=swap">
<style>
:root{
  --red:#e3121c;
  --indigo:#2f2a8c;
  --indigo-deep:#1b185c;
  --ink:#1c1c24;
  --body:#555a66;
  --grey:#d9d9dc;
  --soft:#f2f2f4;
  --lilac:#e6e4fb;
  --footer:#0e0e12;
  --white:#fff;
}
*{box-sizing:border-box;margin:0;padding:0}
html,body{width:1200px;height:4891px;overflow:hidden;background:var(--white)}
body{font-family:"Poppins",sans-serif;color:var(--body);position:relative}
.page{position:relative;width:1200px;height:4891px;overflow:hidden}
.abs{position:absolute}
h2{font-family:"Lato",sans-serif;font-weight:900;color:var(--ink);font-size:34px;letter-spacing:1px;text-align:center}

/* header */
.site-header{top:0;left:0;width:1200px;height:72px;background:var(--white)}
.brand{left:100px;top:8px;display:flex;align-items:center;gap:8px;font-family:"Poppins",sans-serif;font-weight:600;font-size:15px;color:var(--red)}
.brand .mark{width:22px;height:22px;background:var(--red)}
.nav{left:415px;top:25px;display:flex;gap:24px;font-size:14px;color:var(--ink)}
.call{left:838px;top:25px;font-size:14px;color:var(--red)}

/* hero */
.hero{top:72px;left:0;width:1200px;height:498px;background:linear-gradient(120deg,#6e7a5a 0%,#8c8f7a 35%,#4d5440 70%,#2e3328 100%)}
.hero-title{left:582px;top:210px;font-family:"Lato",sans-serif;font-weight:700;font-size:52px;line-height:56px;color:var(--white)}
.hero-copy{left:582px;top:338px;width:520px;font-size:17px;line-height:27px;color:var(--white)}

/* choose band */
.choose{top:570px;left:0;width:1200px;height:100px}
.choose-label{top:592px;left:0;width:1200px;text-align:center;font-family:"Lato",sans-serif;font-weight:700;font-size:19px;color:var(--white)}
.option{top:707px;height:92px;width:316px;background:var(--grey);font-size:16px;color:var(--ink);display:flex;align-items:center;justify-content:center}
.option.active{background:var(--indigo);color:var(--white);box-shadow:0 10px 18px rgba(0,0,0,.35)}

/* about */
.about-photo{top:874px;left:0;width:597px;height:562px;background:linear-gradient(160deg,#8a9a72 0%,#c7b8a0 45%,#3c4a5a 100%)}
.about-bg{top:874px;left:597px;width:603px;height:562px}
.about-title{left:650px;top:1015px;font-family:"Lato",sans-serif;font-weight:900;font-size:36px;color:var(--white)}
.about-text{left:650px;width:450px;font-size:13.5px;line-height:24px;color:#d7d5f2}
.btn{background:var(--red);color:var(--white);font-size:14px;display:flex;align-items:center;justify-content:center}

/* how it works */
.step{width:300px;text-align:center}
.step .ring{margin:0 auto}
.step p{font-size:15px;line-height:26px;color:var(--ink);margin-top:22px}

/* pricing */
.price-card{top:2184px;width:316px;height:414px;background:var(--white);box-shadow:0 6px 18px rgba(0,0,0,.2)}
.price-head{height:70px;background:var(--grey);display:flex;align-items:center;justify-content:center;gap:12px;color:var(--indigo)}
.price-head .qty{font-size:20px}
.price-head .amt{font-family:"Lato",sans-serif;font-weight:900;font-size:44px}
.price-list{list-style:none;padding:18px 28px 0 28px}
.price-list li{position:relative;padding-left:22px;font-size:14px;line-height:26px;color:var(--ink);margin-bottom:18px}
.price-list li::before{content:"";position:absolute;left:2px;top:7px;width:6px;height:10px;border:solid var(--ink);border-width:0 2px 2px 0;transform:rotate(45deg)}
.price-card .btn{position:absolute;left:118px;bottom:28px;width:82px;height:36px;font-size:13px}

/* services */
.service{top:2780px;width:320px;text-align:center}
.service h3{font-family:"Lato",sans-serif;font-weight:900;font-size:22px;color:var(--ink);margin-top:16px}
.service p{font-size:14px;line-height:25px;margin-top:10px}
.channel{top:3159px;width:260px;text-align:center}
.channel .disc{width:104px;height:104px;border-radius:50%;margin:0 auto;border:6px solid #ececf0}
.channel h4{font-family:"Lato",sans-serif;font-weight:900;font-size:17px;margin-top:22px}
.channel p{font-size:14px;line-height:26px;color:var(--ink);margin-top:12px}

/* testimonial */
.testimonial{top:3553px;left:0;width:1200px;height:304px;background:linear-gradient(90deg,var(--indigo-deep),var(--indigo))}
.quote-title{left:100px;top:3625px;font-family:"Lato",sans-serif;font-weight:900;font-size:30px;color:var(--white)}
.quote-text{left:120px;top:3688px;width:740px;font-size:14px;line-height:26px;color:var(--white)}
.quote-mark{font-family:"Lato",sans-serif;font-weight:900;font-size:40px;color:var(--white)}
.avatar{left:928px;top:3608px;width:166px;height:166px;border-radius:50%;border:5px solid var(--white);background:linear-gradient(150deg,#c9a88e,#7b6a62)}

/* faq */
.faq{width:460px;height:72px;display:flex;align-items:center;padding:0 28px;font-size:13.5px;line-height:22px;color:var(--ink)}
.faq.q{background:var(--soft)}
.faq.a{background:var(--lilac);box-shadow:0 4px 10px rgba(60,50,160,.15)}
.faq b{font-weight:600;margin-right:6px}

/* footer */
.footer-bg{top:4482px;left:0;width:1200px;height:409px}
.foot-brand{left:100px;top:4628px;font-weight:600;font-size:15px;color:var(--red);display:flex;align-items:center;gap:8px}
.foot-brand .mark{width:22px;height:22px;background:var(--red)}
.social{left:100px;top:4738px;display:flex;gap:14px}
.social span{width:16px;height:16px;border-radius:50%;background:var(--white)}
.foot-col{top:4632px}
.foot-col h5{font-family:"Lato",sans-serif;font-weight:700;font-size:17px;color:var(--white);margin-bottom:22px}
.foot-col ul{list-style:none}
.foot-col li{font-size:12.5px;color:#cfcfd6;line-height:26px}
.copyright{top:4858px;left:0;width:1200px;text-align:center;font-size:11px;color:#b8b8c0}
.arrow{font-size:40px;color:var(--white);font-family:"Lato",sans-serif}
</style>
</head>
<body>
<div class="page">

  <!-- header -->
  <header class="site-header abs">
    <div class="brand abs"><span class="mark"></span>TallyPorchHelpers</div>
    <nav class="nav abs"><span>About Us</span><span>How It Works</span><span>Pricing</span><span>Services</span><span>Faq</span></nav>
    <div class="call abs">Call Or Text Us : +1-555-014-2290</div>
  </header>

  <!-- hero -->
  <div class="hero abs" role="img" aria-label="Photo of an open house yard sign on a lawn in front of a home"></div>
  <h1 class="hero-title abs">TALLY PORCH<br>HELPERS</h1>
  <p class="hero-copy abs">Helping agents save time and money. We place signs and boost foot traffic to your open houses using proven marketing techniques.</p>

  <svg class="choose abs" width="1200" height="100" viewBox="0 0 1200 100">
    <polygon points="0,0 1200,0 1200,72 630,72 600,98 570,72 0,72" fill="#2f2a8c"/>
  </svg>
  <div class="choose-label abs">CHOOSE THE OPTION BELOW THAT BEST DESCRIBES YOU</div>

  <div class="option abs" style="left:98px">I'M A Full On Brokerage</div>
  <div class="option active abs" style="left:443px">I'M An Ind. Broker With A Team</div>
  <div class="option abs" style="left:786px">I Need Sign Placement Asap</div>

  <!-- about -->
  <div class="about-photo abs" role="img" aria-label="Photo of a couple shaking hands with an agent outside a house"></div>
  <svg class="about-bg abs" width="603" height="562" viewBox="0 0 603 562">
    <defs><linearGradient id="aboutGrad" x1="0" y1="0" x2="1" y2="1"><stop offset="0" stop-color="#2f2a8c"/><stop offset="1" stop-color="#1b185c"/></linearGradient></defs>
    <polygon points="0,0 603,0 603,420 0,562" fill="url(#aboutGrad)"/>
  </svg>
  <h2 class="about-title abs">ABOUT US</h2>
  <p class="about-text abs" style="top:1080px">Helping agents leverage their time and skills to increase production at an affordable price with impeccable support</p>
  <p class="about-text abs" style="top:1150px">Sed ut perspiciatis unde omnis iste natus error sit voluptatem tium doloremque laudantium, totam rem aperiam, eaque ipsa quae ab illo inventore veritatis et quasi architecto beatae vitae dicta sunt oabo. Nemo enim ipsam voluptatem quia voluptas.</p>
  <div class="btn abs" style="left:650px;top:1310px;width:178px;height:44px">Contact Now</div>

  <!-- how it works -->
  <h2 class="abs" style="top:1548px;left:0;width:1200px">HOW IT WORKS</h2>
  <div class="step abs" style="left:117px;top:1625px">
    <svg class="ring" width="140" height="140" viewBox="0 0 140 140"><circle cx="70" cy="70" r="66" fill="none" stroke="#e6e6ea" stroke-width="3"/><path d="M70 4 A66 66 0 1 1 8 92" fill="none" stroke="#2f2a8c" stroke-width="3"/><circle cx="70" cy="70" r="26" fill="#e3121c"/><path d="M70 58 a9 9 0 0 1 9 9 c0 7 -9 15 -9 15 s-9 -8 -9 -15 a9 9 0 0 1 9 -9z" fill="#fff"/><circle cx="70" cy="67" r="3.5" fill="#e3121c"/></svg>
    <p>Place signs strategically in best areas according to where the open house is located</p>
  </div>
  <div class="step abs" style="left:437px;top:1625px">
    <svg class="ring" width="140" height="140" viewBox="0 0 140 140"><circle cx="70" cy="70" r="66" fill="none" stroke="#e6e6ea" stroke-width="3"/><path d="M70 4 A66 66 0 0 1 132 92" fill="none" stroke="#2f2a8c" stroke-width="3"/><circle cx="70" cy="70" r="26" fill="#e3121c"/><path d="M58 76 l12 -14 l12 14 M62 72 v12 h16 v-12" fill="none" stroke="#fff" stroke-width="2.5"/></svg>
    <p>Pick Up the signs after<br>the open house</p>
  </div>
  <div class="step abs" style="left:763px;top:1625px">
    <svg class="ring" width="140" height="140" viewBox="0 0 140 140"><circle cx="70" cy="70" r="66" fill="none" stroke="#e6e6ea" stroke-width="3"/><path d="M70 4 A66 66 0 1 1 4 70" fill="none" stroke="#2f2a8c" stroke-width="3"/><circle cx="70" cy="70" r="26" fill="#e3121c"/><rect x="58" y="62" width="10" height="16" fill="#fff"/><rect x="72" y="62" width="10" height="16" fill="#fff"/></svg>
    <p>Store custom signs for<br>you if needed</p>
  </div>

  <!-- pricing -->
  <svg class="abs" style="top:1917px;left:0" width="1200" height="710" viewBox="0 0 1200 710">
    <defs><linearGradient id="priceGrad" x1="0" y1="0" x2="1" y2="1"><stop offset="0" stop-color="#332d96"/><stop offset="1" stop-color="#1b185c"/></linearGradient></defs>
    <polygon points="0,0 1200,110 1200,560 0,600" fill="url(#priceGrad)"/>
  </svg>
  <h2 class="abs" style="top:2073px;left:0;width:1200px;color:#fff">PRICING</h2>
  <div class="arrow abs" style="left:36px;top:2400px">‹</div>
  <div class="arrow abs" style="left:1140px;top:2400px">›</div>

  <div class="price-card abs" style="left:98px">
    <div class="price-head"><span class="qty">5 SIGNS</span><span class="amt">$49</span></div>
    <ul class="price-list"><li>Place signs strategically in best areas according to where the open house is located</li><li>Pick Up the signs after the open house</li><li>Store custom signs for you if needed</li></ul>
    <div class="btn">Buy Now</div>
  </div>
  <div class="price-card abs" style="left:443px">
    <div class="price-head"><span class="qty">10 SIGNS</span><span class="amt">$59</span></div>
    <ul class="price-list"><li>Place signs strategically in best areas according to where the open house is located</li><li>Pick Up the signs after the open house</li><li>Store custom signs for you if needed</li></ul>
    <div class="btn">Buy Now</div>
  </div>
  <div class="price-card abs" style="left:786px">
    <div class="price-head"><span class="qty">15 SIGNS</span><span class="amt">$69</span></div>
    <ul class="price-list"><li>Place signs strategically in best areas according to where the open house is located</li><li>Pick Up the signs after the open house</li><li>Store custom signs for you if needed</li></ul>
    <div class="btn">Buy Now</div>
  </div>

  <!-- services -->
  <h2 class="abs" style="top:2700px;left:0;width:1200px">SERVICES</h2>
  <div class="service abs" style="left:94px">
    <svg width="44" height="44" viewBox="0 0 44 44"><circle cx="22" cy="22" r="18" fill="none" stroke="#e3121c" stroke-width="4"/><path d="M22 12 v10 l7 5" fill="none" stroke="#e3121c" stroke-width="4"/></svg>
    <h3>LOREM IPSUM</h3><p>At vero eos et accusamus et<br>iusto odio dignissimos ducimus<br>qui blanditiis praesentium</p>
  </div>
  <div class="service abs" style="left:440px">
    <svg width="44" height="44" viewBox="0 0 44 44"><text x="22" y="38" text-anchor="middle" font-family="Lato,sans-serif" font-weight="900" font-size="42" fill="#e3121c">$</text></svg>
    <h3>LOREM IPSUM</h3><p>At vero eos et accusamus et<br>iusto odio dignissimos ducimus<br>qui blanditiis praesentium</p>
  </div>
  <div class="service abs" style="left:786px">
    <svg width="48" height="44" viewBox="0 0 48 44"><circle cx="24" cy="14" r="7" fill="#e3121c"/><circle cx="10" cy="18" r="5" fill="#e3121c"/><circle cx="38" cy="18" r="5" fill="#e3121c"/><path d="M12 38 a12 12 0 0 1 24 0z M2 36 a8 8 0 0 1 14 -5 M46 36 a8 8 0 0 0 -14 -5" fill="#e3121c"/></svg>
    <h3>LOREM IPSUM</h3><p>At vero eos et accusamus et<br>iusto odio dignissimos ducimus<br>qui blanditiis praesentium</p>
  </div>

  <h2 class="abs" style="top:3052px;left:0;width:1200px;font-size:26px;line-height:38px">SIGN UP FOR A SUBSCRIPTION AND GET THESE<br>MARKETING SERVICES FOR FREE</h2>
  <div class="channel abs" style="left:79px"><div class="disc" style="background:#e3121c"></div><h4 style="color:#e3121c">SMS</h4><p>Send sms blast to your neighborhood informing them your home is for sale and if they know anyone looking to send them over.</p></div>
  <div class="channel abs" style="left:336px"><div class="disc" style="background:#1f5c99"></div><h4 style="color:#1f5c99">EMAIL</h4><p>Send Email blast to your neighborhood informing them your home is for sale and if they know anyone looking to send them over.</p></div>
  <div class="channel abs" style="left:597px"><div class="disc" style="background:#2f4f8f"></div><h4 style="color:#2f4f8f">SOCIAL AD</h4><p>Newsfeed ads to<br>people in your open house</p></div>
  <div class="channel abs" style="left:858px"><div class="disc" style="background:#5b2a86"></div><h4 style="color:#5b2a86">VB</h4><p>Send VB blast to your neighborhood informing them your home is for sale and if they know anyone looking to send them over.</p></div>

  <!-- testimonial -->
  <div class="testimonial abs"></div>
  <div class="quote-title abs">CUSTOMER SAY'S</div>
  <div class="quote-mark abs" style="left:94px;top:3670px">“</div>
  <p class="quote-text abs">Lorem ipsum dolor sit amet, consectetur adipiscing elit, sed do eiusmod tempor incididunt ut labore et dolore magna aliqua. Ut enim ad minim veniam, quis nostrud exercitation ullamco laboris nisi ut aliquip ex ea commodo consequat.</p>
  <div class="quote-mark abs" style="left:322px;top:3752px">”</div>
  <div class="avatar abs" role="img" aria-label="Portrait photo of a client"></div>
  <div class="abs" style="left:928px;top:3790px;width:166px;text-align:center;font-size:12px;font-weight:600;color:#fff">MARA FIELDING</div>
  <div class="arrow abs" style="left:42px;top:3680px">‹</div>
  <div class="arrow abs" style="left:1140px;top:3680px">›</div>

  <!-- faq -->
  <h2 class="abs" style="top:3957px;left:0;width:1200px">FAQ</h2>
  <div class="faq q abs" style="left:124px;top:4036px"><span><b>Q)</b>At vero eos et accusamus et iusto odio dignissimos mus qui blanditiis praesentium ?</span></div>
  <div class="faq a abs" style="left:620px;top:4036px"><span><b>A)</b>At vero eos et accusamus et iusto odio dignissimos mus qui blanditiis praesentium</span></div>
  <div class="faq q abs" style="left:124px;top:4153px"><span><b>Q)</b>At vero eos et accusamus et iusto odio dignissimos mus qui blanditiis praesentium ?</span></div>
  <div class="faq a abs" style="left:620px;top:4153px"><span><b>A)</b>At vero eos et accusamus et iusto odio dignissimos mus qui blanditiis praesentium</span></div>
  <div class="faq q abs" style="left:124px;top:4274px"><span><b>Q)</b>At vero eos et accusamus et iusto odio dignissimos mus qui blanditiis praesentium ?</span></div>
  <div class="faq a abs" style="left:620px;top:4274px"><span><b>A)</b>At vero eos et accusamus et iusto odio dignissimos mus qui blanditiis praesentium</span></div>
  <div class="btn abs" style="left:542px;top:4398px;width:116px;height:40px">View All</div>

  <!-- footer -->
  <svg class="footer-bg abs" width="1200" height="409" viewBox="0 0 1200 409">
    <polygon points="0,0 600,60 1200,0 1200,409 0,409" fill="#0e0e12"/>
  </svg>
  <div class="foot-brand abs"><span class="mark"></span>TallyPorchHelpers</div>
  <div class="social abs"><span></span><span></span><span></span><span></span><span></span></div>
  <div class="foot-col abs" style="left:368px"><h5>Links</h5><ul><li>How it works</li><li>Service</li><li>Pricing</li><li>About us</li><li>Faq</li></ul></div>
  <div class="foot-col abs" style="left:545px"><h5>Helpful Links</h5><ul><li>Open House</li><li>Sign Up</li><li>Careers</li><li>Contact</li></ul></div>
  <div class="foot-col abs" style="left:730px"><h5>Legal</h5><ul><li>Terms &amp; Conditions</li><li>Faq</li><li>Privacy Policy</li><li>Disclaimers</li></ul></div>
  <div class="foot-col abs" style="left:928px"><h5>Contact Us</h5><ul>
    <li><svg width="12" height="12" viewBox="0 0 12 12" style="margin-right:12px;vertical-align:-1px"><rect width="12" height="12" rx="2" fill="#fff"/><path d="M3.5 2.5 l1.5 2 l-1 1 a5 5 0 0 0 2.5 2.5 l1 -1 l2 1.5 l-1 1.5 a7 7 0 0 1 -6 -6z" fill="#0e0e12"/></svg>1 555 017 4408</li>
    <li><svg width="12" height="10" viewBox="0 0 12 10" style="margin-right:12px;vertical-align:0"><rect width="12" height="10" fill="#fff"/><path d="M0 0 l6 5 l6 -5" fill="none" stroke="#0e0e12"/></svg>hello@tallyporchhelpers.net</li>
  </ul></div>
  <div class="copyright abs">© 2018 Copyrights TallyPorchHelpers All Rights Reserved</div>

</div>
</body>
</html>
```